Simple Logo Design for Semi-Clear Plastic Frosted Card stock

Create a business card on frosted plastic. compliment existing logo elements with a tree trunk, roots, or seed at the lower half and the full logo both on the front.

Contact information will go on a solid portion of the back of this design since this card stock is semi-transparent.

It is important to consider this plastic card stock medium in your design. I found helpful tips and guides listed at vellaprint-sample.net: be careful to understand ink printed on plastic cards cannot have too much of a consistent print area or risks peeling and fine lines can easily scratch off.
Updates

2" x 3.5" 20PT Clear Plastic Business cards with Round corners Please get info or templates here: https://www.vellaprint-sample.net/product-detail/2-x-35-20pt-clear-plastic-business-cards-with-round-corners

Target Market(s)

Not for profit- religion

Industry/Entity Type

Business

Must include complementary elements to the existing logo

Font styles to use
Decorative

Colors
000000

Requirements
Must have
• Elements of community, nature and oneness. Such as: seed, roots, tree trunk, etc.
• Three lines of space on the back for Name, Title, Phone Number.
Nice to have
• I like a light use of decorative elements
Should not have
• No eyes, from faces or animals.

```html
<!DOCTYPE html>
<html lang="en">
<head>
<meta charset="utf-8">
<title>Steadfast Grove – Business Card</title>
<link rel="stylesheet" href="https://fonts.googleapis.com/css2?family=Josefin+Sans:wght@400;600&family=Mulish:wght@400;600&display=swap">
<style>
  :root {
    --page-bg: #cfc6ba;
    --frost-top: rgba(255,255,255,0.62);
    --frost-bottom: rgba(244,246,245,0.48);
    --frost-edge: rgba(255,255,255,0.9);
    --evergreen: #12413c;
    --evergreen-deep: #0b302c;
    --leaf: #3f7d3a;
    --blush: #e6d2cb;
    --cream-gold: #ddd3b4;
    --ink: #1d3b36;
  }
  html, body {
    margin: 0;
    padding: 0;
    width: 1200px;
    height: 969px;
    overflow: hidden;
    background: var(--page-bg);
  }
  .canvas {
    position: relative;
    width: 1200px;
    height: 969px;
  }
  .card {
    position: absolute;
    left: 100px;
    top: 201px;
    width: 1000px;
    height: 567px;
    border-radius: 32px;
    overflow: hidden;
    background:
      radial-gradient(ellipse at 30% 20%, rgba(255,255,255,0.35) 0%, rgba(255,255,255,0) 60%),
      linear-gradient(160deg, var(--frost-top) 0%, var(--frost-bottom) 100%);
    box-shadow: inset 0 0 0 2px var(--frost-edge), 0 14px 34px rgba(0,0,0,0.14);
  }
  .card-wave {
    position: absolute;
    inset: 0;
    width: 100%;
    height: 100%;
  }
  .brand {
    position: absolute;
    left: 70px;
    top: 214px;
  }
  .brand-row {
    display: flex;
    align-items: center;
    gap: 14px;
    white-space: nowrap;
  }
  .brand-dot {
    width: 26px;
    height: 26px;
    border-radius: 50%;
    background: var(--evergreen);
    flex: none;
  }
  .brand-name {
    font-family: "Josefin Sans", sans-serif;
    font-weight: 600;
    font-size: 44px;
    letter-spacing: 1px;
    text-transform: uppercase;
    color: var(--evergreen);
    line-height: 1;
    padding-top: 6px;
  }
  .brand-tagline {
    margin: 6px 0 0 40px;
    font-family: "Josefin Sans", sans-serif;
    font-weight: 600;
    font-size: 15px;
    letter-spacing: 1.5px;
    text-transform: uppercase;
    color: var(--ink);
    white-space: nowrap;
  }
  .contact {
    position: absolute;
    right: 60px;
    top: 372px;
    text-align: right;
    font-family: "Mulish", sans-serif;
    color: var(--cream-gold);
  }
  .contact-name {
    font-size: 31px;
    font-weight: 600;
    letter-spacing: 1.5px;
    text-transform: uppercase;
    margin: 0;
  }
  .contact-title {
    font-size: 27px;
    font-weight: 400;
    letter-spacing: 1px;
    text-transform: uppercase;
    margin: 10px 0 0;
  }
  .contact-phone {
    font-size: 29px;
    font-weight: 400;
    letter-spacing: 1.5px;
    margin: 18px 0 0;
  }
</style>
</head>
<body>
<main class="canvas">
  <section class="card" aria-label="Business card front">
    <svg class="card-wave" viewBox="0 0 1000 567" preserveAspectRatio="none" aria-hidden="true">
      <defs>
        <linearGradient id="bandFill" x1="0" y1="0" x2="1" y2="1">
          <stop offset="0" stop-color="#1b4a44" stop-opacity="0.93"/>
          <stop offset="1" stop-color="#0b302c" stop-opacity="0.96"/>
        </linearGradient>
        <linearGradient id="innerSwoosh" x1="0" y1="0" x2="1" y2="0">
          <stop offset="0" stop-color="#3f7d3a"/>
          <stop offset="0.45" stop-color="#3f7d3a"/>
          <stop offset="0.75" stop-color="#2a5f45"/>
          <stop offset="1" stop-color="#1b4a44"/>
        </linearGradient>
      </defs>
      <path d="M0,395 C120,445 260,470 400,440 C600,395 760,275 1000,250 L1000,567 L0,567 Z" fill="url(#bandFill)"/>
      <path d="M0,360 C140,420 290,455 430,430 C620,395 780,280 1000,240" fill="none" stroke="var(--leaf)" stroke-width="10" stroke-linecap="round"/>
      <path d="M0,385 C150,440 300,468 450,442 C640,408 800,292 1000,258" fill="none" stroke="var(--blush)" stroke-width="3"/>
      <path d="M0,412 C130,458 280,480 420,458 C610,428 790,310 1000,274" fill="none" stroke="url(#innerSwoosh)" stroke-width="5"/>
    </svg>

    <div class="brand">
      <div class="brand-row">
        <span class="brand-dot"></span>
        <span class="brand-name">Steadfast Grove</span>
      </div>
      <p class="brand-tagline">Wisdom, Fellowship &amp; Calm</p>
    </div>

    <div class="contact">
      <p class="contact-name">Alan Merrow</p>
      <p class="contact-title">President</p>
      <p class="contact-phone">555 0142 3867</p>
    </div>
  </section>
</main>
</body>
</html>
```